Redesign a Start-Up Dating Website

Website: https://morvelique.com.
Make sure the design has an island style theme.
I would like the 7 pages of my website to have a new and professional look. I want the same colors to remain, but I want a creative look for all the pages. This is a dating website that is in the startup stage. So, I want to give my entire website a custom makeover. I want something that will stand out from the other dating sites. Something that will attract more people to want to use my services, and hopefully get new members.
Target Market(s)
Dating
Industry/Entity Type
Dating
Coding
Coded - Design and coding required
Number of Pages Required
5+ page
Font styles to use
Other font styles liked:
- Decorative, San Serif
Requirements
Must have
- The design must have the original colors and a stylish font to go along. The design must be creative, welcoming, and professional. I would like an island style theme for the website. This is a dating website so make sure that the design is tailored to that aspect.
Nice to have
- It would be nice to have a decorative font and a professional style on all the pages. Make sure the design will be mobile responsive and friendly for all the pages on the website.
Should not have
- The design should not be bland and uncreative.

```html
<!DOCTYPE html>
<html lang="en">
<head>
<meta charset="utf-8">
<title>Morvelique – Island Dating</title>
<link rel="stylesheet" href="https://fonts.googleapis.com/css2?family=Raleway:wght@400;500;600;700&family=Open+Sans:wght@400;600&display=swap">
<style>
:root{
  --teal:#3db59d;
  --teal-dark:#2fa58e;
  --orange:#f28c1f;
  --purple:#6b3f9a;
  --ink:#2b2b2b;
  --muted:#555;
  --line:#dcdcdc;
  --white:#fff;
}
*{box-sizing:border-box;margin:0;padding:0}
html,body{width:723px;height:1200px;overflow:hidden;background:var(--white)}
body{font-family:"Open Sans",Arial,sans-serif;color:var(--ink)}
.page{position:relative;width:723px;height:1200px;overflow:hidden}
.abs{position:absolute}
h1,h2,h3,.nav,.brand{font-family:"Raleway",Arial,sans-serif}

/* header */
.site-header{position:absolute;left:0;top:0;width:723px;height:50px;border-bottom:2px solid var(--teal);background:var(--white)}
.brand{position:absolute;left:98px;top:14px;display:flex;align-items:center;gap:6px;font-size:19px;font-weight:700;color:var(--teal)}
.brand-dot{width:24px;height:24px;border-radius:50%;background:var(--orange)}
.nav{position:absolute;left:246px;top:0;display:flex;height:48px;font-size:7px;font-weight:600;text-transform:uppercase}
.nav a{display:flex;align-items:center;padding:0 9px;color:var(--ink);text-decoration:none}
.nav a.active{background:var(--teal);color:var(--white);padding:0 10px}
.nav a.login{color:var(--teal);margin-left:4px;padding-right:4px}
.nav a.register{color:var(--orange);padding-left:4px}

/* hero */
.hero{position:absolute;left:0;top:50px;width:723px;height:312px;background:linear-gradient(110deg,#8a6a44 0%,#c9a87a 35%,#e8dcc8 60%,#d9c8a8 100%)}
.hero-arrow{position:absolute;top:134px}
.join-card{position:absolute;left:425px;top:55px;width:200px;height:196px;background:var(--white);border-bottom:5px solid var(--orange);padding:17px 14px 0}
.join-card h2{text-align:center;font-size:13px;font-weight:500;letter-spacing:.2px;padding-bottom:10px;border-bottom:1px dotted #aaa}
.join-card h2 span{color:var(--orange);font-weight:700}
.gender-row{display:flex;justify-content:space-between;margin-top:9px;font-size:7px}
.gender{display:flex;align-items:flex-end;gap:4px}
.gender .opts{display:flex;gap:8px}
.opt{display:flex;flex-direction:column;align-items:center;font-size:6px;gap:2px}
.ring{width:15px;height:15px;border-radius:50%;border:2px solid var(--teal)}
.ring.purple{border-color:var(--purple)}
.field-row{display:flex;align-items:center;gap:2px;margin-top:10px}
.field{width:77px;height:18px;border:1px solid #bbb;font-size:7px;display:flex;align-items:center;justify-content:space-between;padding:0 5px}
.field i{width:0;height:0;border-left:2.5px solid transparent;border-right:2.5px solid transparent;border-top:3px solid #444}
.to{font-size:5px;color:var(--orange);width:4px}
.btn-arrow{position:relative;display:inline-flex;align-items:center;justify-content:center;color:var(--white);font-family:"Raleway",Arial,sans-serif;font-weight:700;font-size:7px;text-transform:uppercase}
.btn-arrow::after{content:"";position:absolute;right:-7px;top:0;border-top:9px solid transparent;border-bottom:9px solid transparent;border-left:7px solid currentColor}
.search-btn{margin:15px 0 0 50px;width:101px;height:18px;background:var(--teal)}
.search-btn::after{border-left-color:var(--teal)}

/* community */
.section-title{position:absolute;width:723px;text-align:center;font-family:"Raleway",Arial,sans-serif;font-weight:500;font-size:13px}
.section-title span{color:var(--orange);font-weight:700}
.members{position:absolute;left:96px;top:423px;display:flex;gap:9px}
.member{width:99px;height:133px;border:1px solid var(--line);text-align:center}
.member.selected{border-color:var(--purple)}
.member .photo{height:84px}
.member .name{color:var(--teal);font-size:8px;margin-top:3px}
.member .meta{font-size:6px;color:var(--ink);margin-top:1px;padding-bottom:5px;border-bottom:1px solid var(--line)}
.member .more{font-size:6.5px;color:var(--purple);margin-top:6px}
.chev{position:absolute;top:463px;color:var(--teal);font-size:12px}

/* promo band */
.promo{position:absolute;left:0;top:597px;width:723px;height:160px;background:linear-gradient(90deg,#3ab09b 0%,#8fae6a 50%,#e39a37 100%);text-align:center;color:var(--white)}
.promo h2{margin-top:38px;font-size:12.5px;font-weight:500}
.promo p{margin-top:12px;font-family:"Raleway",Arial,sans-serif;font-size:7.5px;line-height:13px;text-transform:uppercase}
.signup-btn{margin-top:12px;width:106px;height:18px;background:var(--purple);color:var(--purple)}
.signup-btn span{color:var(--white)}

/* features */
.step{position:absolute;left:97px;display:flex;gap:15px}
.step-icon{width:52px;height:51px;background:var(--orange);display:flex;align-items:center;justify-content:center}
.step h3,.benefit h3{font-size:9px;font-weight:600;color:var(--purple);margin-top:2px}
.step p,.benefit p{font-size:6px;line-height:13px;color:var(--ink);margin-top:6px}
.step p{width:172px}
.benefits-title{position:absolute;left:389px;top:792px;font-family:"Raleway",Arial,sans-serif;font-size:12.5px;font-weight:500}
.pager{position:absolute;top:791px;width:15px;height:15px;border-radius:50%;border:1px solid var(--line);color:var(--teal);font-size:8px;display:flex;align-items:center;justify-content:center}
.benefit{position:absolute;left:389px;display:flex;gap:12px}
.benefit-icon{width:52px;height:52px;border-radius:50%;background:var(--teal);display:flex;align-items:center;justify-content:center;flex:none}
.benefit p{width:182px}

/* footer */
.site-footer{position:absolute;left:0;top:1032px;width:723px;height:168px;background:var(--teal);border-top:2px solid var(--purple);color:var(--white)}
.site-footer h3{position:absolute;top:24px;font-size:9px;font-weight:600;text-transform:uppercase}
.footer-photo{position:absolute;left:97px;top:41px;width:94px;height:64px;border:2px solid var(--white);background:linear-gradient(120deg,#5a8fb0,#d8b68a 60%,#c9775a)}
.about-text{position:absolute;left:204px;top:41px;width:140px;font-size:6px;line-height:12.3px}
.mail{position:absolute;left:204px;top:99px;font-size:7px;font-weight:600}
.links{position:absolute;left:380px;top:40px;list-style:none;font-size:6px;line-height:12.2px}
.sub-input{position:absolute;left:475px;width:150px;height:19px;border:1px solid var(--white);font-size:6px;padding:5px}
.subscribe-btn{position:absolute;left:475px;top:84px;width:63px;height:18px;background:var(--orange);color:var(--orange)}
.subscribe-btn span{color:var(--white)}
.footer-rule{position:absolute;left:97px;top:132px;width:528px;border-top:1px solid rgba(255,255,255,.35)}
.socials{position:absolute;left:97px;top:143px;display:flex;gap:3px}
.socials i{width:15px;height:15px;border-radius:50%;border:1px solid var(--white)}
.copyright{position:absolute;left:474px;top:148px;font-size:6.5px}
</style>
</head>
<body>
<div class="page">

  <header class="site-header">
    <div class="brand"><span class="brand-dot"></span>Morvelique</div>
    <nav class="nav">
      <a class="active" href="#">Home</a><a href="#">Search</a><a href="#">Members</a><a href="#">Extras</a><a href="#">About</a><a href="#">Premium</a><a href="#">Contact</a><a class="login" href="#">Login</a><a class="register" href="#">Register</a>
    </nav>
  </header>

  <section class="hero" role="img" aria-label="Smiling couple in sun hats and sunglasses on a sunny beach">
    <svg class="hero-arrow" style="left:14px" width="22" height="44" viewBox="0 0 22 44"><polyline points="20,1 2,22 20,43" fill="none" stroke="#fff" stroke-width="1.2"/></svg>
    <svg class="hero-arrow" style="left:692px" width="22" height="44" viewBox="0 0 22 44"><polyline points="2,1 20,22 2,43" fill="none" stroke="#fff" stroke-width="1.2"/></svg>
    <form class="join-card">
      <h2>JOIN <span>FREE</span> TODAY</h2>
      <div class="gender-row">
        <div class="gender">I am a <div class="opts"><div class="opt">Man<span class="ring"></span></div><div class="opt">Woman<span class="ring purple"></span></div></div></div>
        <div class="gender">Seeking a <div class="opts"><div class="opt">Man<span class="ring"></span></div><div class="opt">Woman<span class="ring purple"></span></div></div></div>
      </div>
      <div class="field-row"><div class="field">Age<i></i></div><span class="to">to</span><div class="field">99<i></i></div></div>
      <div class="field-row"><div class="field">Country<i></i></div><span class="to"></span><div class="field">Zipcode</div></div>
      <div class="btn-arrow search-btn">Search here</div>
    </form>
  </section>

  <h2 class="section-title" style="top:388px">JOIN THIS COMMUNITY OF <span>1 MORVELIQUE</span> MEMBERS</h2>
  <span class="chev" style="left:72px">&#8249;</span>
  <span class="chev" style="left:642px">&#8250;</span>
  <div class="members">
    <div class="member selected"><div class="photo" role="img" aria-label="Member profile photo" style="background:linear-gradient(135deg,#c24a3a,#e7b9a0)"></div><div class="name">IslaRae</div><div class="meta">-63, Germany</div><div class="more">View More</div></div>
    <div class="member"><div class="photo" role="img" aria-label="Member profile photo" style="background:linear-gradient(135deg,#4a3a30,#2a2a3a)"></div><div class="name">tomaso</div><div class="meta">28, United States</div><div class="more">View More</div></div>
    <div class="member"><div class="photo" role="img" aria-label="Member profile photo" style="background:linear-gradient(135deg,#d8c7a8,#6b4630)"></div><div class="name">Name</div><div class="meta">23, United States</div><div class="more">View More</div></div>
    <div class="member"><div class="photo" role="img" aria-label="Member profile photo" style="background:linear-gradient(135deg,#3a4a40,#c89a80)"></div><div class="name">Name</div><div class="meta">27, Canada</div><div class="more">View More</div></div>
    <div class="member"><div class="photo" role="img" aria-label="Member profile photo" style="background:linear-gradient(135deg,#8a8a88,#d8b59a)"></div><div class="name">Lunara</div><div class="meta">26, United States</div><div class="more">View More</div></div>
  </div>

  <section class="promo">
    <h2>DATING IS EASY WITH MORVELIQUE</h2>
    <p>Sign-up for a <b>30 days free trial</b> enjoy all the benefits<br>Morvelique has to offer with a full membership.</p>
    <div class="btn-arrow signup-btn"><span>Sign up free</span></div>
  </section>

  <div class="step" style="top:794px">
    <div class="step-icon"><svg width="26" height="26" viewBox="0 0 26 26" fill="#fff"><circle cx="12" cy="8" r="6"/><path d="M1 25c0-7 5-11 11-11s11 4 11 11z"/></svg></div>
    <div><h3>CREATE A PROFILE</h3><p>Let people know all about you; the good and the quirky -show the world your true colors and find someone with the same unique qualities as you.</p></div>
  </div>
  <div class="step" style="top:870px">
    <div class="step-icon"><svg width="28" height="28" viewBox="0 0 28 28"><circle cx="11" cy="8" r="6" fill="#fff"/><path d="M0 25c0-7 5-11 11-11 3 0 5 1 6 2v9z" fill="#fff"/><circle cx="20" cy="19" r="5" fill="none" stroke="#fff" stroke-width="2"/><line x1="23.5" y1="22.5" x2="27" y2="26" stroke="#fff" stroke-width="2.5"/></svg></div>
    <div><h3>FIND MATCHES</h3><p>Browse other users and feel the excitement of getting your first message and getting to know potential dates in a safe and fun environment.</p></div>
  </div>
  <div class="step" style="top:944px">
    <div class="step-icon"><svg width="26" height="26" viewBox="0 0 26 26" fill="#fff"><path d="M13 23C4 16 2 12 2 8a5.5 5.5 0 0 1 11-1 5.5 5.5 0 0 1 11 1c0 4-2 8-11 15z"/></svg></div>
    <div><h3>START DATING</h3><p>Once you've found your potential soulmate, it's time to meet up and say 'Hello' to the start of your journey together.</p></div>
  </div>

  <h2 class="benefits-title">BENEFITS</h2>
  <span class="pager" style="left:588px">&#8249;</span>
  <span class="pager" style="left:609px">&#8250;</span>
  <div class="benefit" style="top:820px">
    <div class="benefit-icon"><svg width="24" height="24" viewBox="0 0 24 24" fill="#fff"><path d="M9 3h6l-2 4h-2z"/><path d="M12 8c-6 0-9 6-9 10 0 3 3 4 9 4s9-1 9-4c0-4-3-10-9-10z"/><text x="12" y="19" text-anchor="middle" font-size="8" font-family="Arial" fill="#3db59d">$</text></svg></div>
    <div><h3>AFFORDABLE</h3><p>Lorem ipsum dolor sit amet, consecte tur adipisc elit dolroin ultricies vestibulum velit. bibsit amet, conenducoentum.</p></div>
  </div>
  <div class="benefit" style="top:877px">
    <div class="benefit-icon"><svg width="24" height="24" viewBox="0 0 24 24" fill="none" stroke="#fff" stroke-width="1.8"><rect x="3" y="4" width="15" height="17"/><line x1="6" y1="9" x2="14" y2="9"/><line x1="6" y1="13" x2="12" y2="13"/><line x1="10" y1="18" x2="22" y2="4"/></svg></div>
    <div><h3>EASY SIGN-UP</h3><p>Lorem ipsum dolor sit amet, consecte tur adipisc elit dolroin ultricies vestibulum velit. bibsit amet, conenducoentum.</p></div>
  </div>
  <div class="benefit" style="top:934px">
    <div class="benefit-icon"><svg width="24" height="24" viewBox="0 0 24 24" fill="none" stroke="#fff" stroke-width="1.8"><rect x="4" y="4" width="13" height="17"/><rect x="8" y="2" width="5" height="4" fill="#fff"/><line x1="7" y1="10" x2="14" y2="10"/><circle cx="18" cy="18" r="4.5" fill="#3db59d"/><path d="M16 16l4 4M20 16l-4 4"/></svg></div>
    <div><h3>CANCELLATION PROCESSES</h3><p>Lorem ipsum dolor sit amet, consecte tur adipisc elit dolroin ultricies vestibulum velit. bibsit amet, conenducoentum.</p></div>
  </div>

  <footer class="site-footer">
    <h3 style="left:98px">About</h3>
    <div class="footer-photo" role="img" aria-label="Happy couple in hats smiling outdoors"></div>
    <p class="about-text">Morvelique aims to provide a straight-forward, easy-to-use online dating service. I won't over-complicate things or reduce the amount of people you can talk to with algorithms.</p>
    <div class="mail">&#9993; contact@morvelique.com</div>
    <h3 style="left:379px">Quick links</h3>
    <ul class="links"><li>Morvelique</li><li>About</li><li>Contact</li><li>Login</li><li>Members</li><li>Premium</li></ul>
    <h3 style="left:474px">Subscribe for updates</h3>
    <div class="sub-input" style="top:40px">Name:</div>
    <div class="sub-input" style="top:62px">Email:</div>
    <div class="btn-arrow subscribe-btn"><span>Subscribe</span></div>
    <div class="footer-rule"></div>
    <div class="socials" aria-label="Social links"><i></i><i></i><i></i><i></i></div>
    <p class="copyright">Copyright &copy; Morvelique 2017 . All rights reserved.</p>
  </footer>

</div>
</body>
</html>
```